PWNF Traditional Business Card Project

Please see attached....just a simple business card... on attachment- please use the exact font, style, etc as the attached "Ned Farley Broughton" card... however, replace with the "Walter Augustin Pryde" text and address below the card.

```html
<!DOCTYPE html>
<html lang="en">
<head>
<meta charset="utf-8">
<title>PWNF Business Card – Walter Augustin Pryde</title>
<link rel="stylesheet" href="https://fonts.googleapis.com/css2?family=Old+Standard+TT:wght@400;700&family=Montserrat:wght@400;500&display=swap">
<style>
  :root {
    --backdrop: #2b2a27;
    --card: #fdfdfc;
    --ink: #141414;
    --ink-soft: #2e2e2e;
  }
  * { margin: 0; padding: 0; box-sizing: border-box; }
  html, body {
    width: 1200px; height: 801px; overflow: hidden;
    background: var(--backdrop);
  }
  .business-card {
    position: absolute;
    left: 90px; top: 98px;
    width: 1020px; height: 605px;
    background: var(--card);
    color: var(--ink);
    box-shadow: 0 10px 30px rgba(0,0,0,0.45);
  }
  .firm-name {
    position: absolute; left: 58px; top: 52px;
    font-family: "Old Standard TT", serif;
    font-weight: 700;
    font-size: 46px;
    font-variant: small-caps;
    letter-spacing: 1px;
    line-height: 1;
  }
  .firm-suffix {
    position: absolute; left: 150px; top: 104px;
    font-family: "Old Standard TT", serif;
    font-weight: 700;
    font-size: 19px;
    letter-spacing: 1.5px;
    color: var(--ink-soft);
  }
  .person {
    position: absolute; left: 0; right: 0; top: 262px;
    text-align: center;
  }
  .person-name {
    font-family: "Old Standard TT", serif;
    font-weight: 700;
    font-size: 40px;
    letter-spacing: 1.5px;
    text-transform: uppercase;
    line-height: 1;
  }
  .person-title {
    margin-top: 14px;
    font-family: "Montserrat", sans-serif;
    font-weight: 400;
    font-size: 22px;
    letter-spacing: 3px;
    text-transform: uppercase;
    color: var(--ink-soft);
  }
  .person-rule {
    width: 150px; height: 3px;
    margin: 18px auto 0;
    background: var(--ink);
  }
  .contact {
    position: absolute;
    font-family: "Montserrat", sans-serif;
    font-weight: 400;
    font-size: 18px;
    letter-spacing: 3px;
    line-height: 30px;
    text-transform: uppercase;
    color: var(--ink-soft);
  }
  .contact-address { left: 58px; top: 430px; }
  .contact-lines { right: 58px; top: 470px; }
  .contact .label { display: inline-block; width: 40px; }
</style>
</head>
<body>
  <article class="business-card">
    <h1 class="firm-name">Pacific West Northfield</h1>
    <p class="firm-suffix">LAWYERS, PLC</p>

    <section class="person">
      <h2 class="person-name">Walter Augustin Pryde</h2>
      <p class="person-title">Attorney at Law</p>
      <div class="person-rule"></div>
    </section>

    <address class="contact contact-address">
      2740 Cedar Avenue, Suite B<br>
      Alder Hills, CA 91802<br>
      <span class="label">W :</span>www.lawspwnf.com
    </address>

    <address class="contact contact-lines">
      <span class="label">P :</span>(555) 284-7310<br>
      <span class="label">F :</span>(555) 284-7311<br>
      <span class="label">M :</span>wpryde@lawspwnf.com
    </address>
  </article>
</body>
</html>
```